Illustrations, Icons and placement

Wire frame will describe it best, https://plavido.com/diagrams/kRtmWbNoQeprsLvx

With the direction of my mockups I am going to require illustrations with similarity to the mock up. I need icons for my slider and of course beautiful slides. It is not necessary to design the webpage, I know where I want to go with this, I really just need strong illustrations.

This is the first serious design submitted. I appreciate the obvious hard work. To be honest, this system is not great for designers to know exactly what I want but finding a designer that can put in the effort to get there is the trick.

I have locked in the front page design to something that is very accurately portrayed in the mockup. The reason why is the illustration I will using. Currently My mock up shows flower on a hill, i replace with an brightcrate illustration, see uploaded file to review... Also, colors are definatly what I am looking for but this ok for now. Your design is good..

Reason: my choice needs more time to finish the design before we begin

Target Market(s)

SaaS Consumer

Industry/Entity Type

Work

Requirements
Must have
• Display features in a nice slider like

http://www.drovelink.com/pebblegate/index.php

room in header for new illustration, see attachment
Should not have
• Traditional out dated designs that look like templates

```html
<!DOCTYPE html>
<html lang="en">
<head>
<meta charset="utf-8">
<title>Team Sites – Features</title>
<link rel="stylesheet" href="https://fonts.googleapis.com/css2?family=Tinos:wght@400;700&family=Source+Sans+3:wght@400;600&display=swap">
<style>
  :root {
    --page-bg: #060606;
    --band-top: #140d07;
    --band-glow: #2a1a0c;
    --nav-label: #8f7462;
    --nav-active: #a892cc;
    --icon-dark: #0d0d0d;
    --icon-purple: #a88dc9;
    --heading-purple: #9a7cb2;
    --body-brown: #8d6c5d;
    --read-more: #d4901f;
    --divider: #8a5a34;
    --panel-bg: #000000;
    --panel-glow: #2c1a08;
    --tab-top: #5b437a;
    --tab-bottom: #66288a;
    --tab-text: #e8e0ef;
    --section-title: #9c6e2e;
    --light-text: #cdd6da;
    --button-top: #6fd23f;
    --button-bottom: #47b122;
    --button-text: #12300a;
    --device-light: #4a4a4a;
    --device-dark: #111111;
  }
  * { box-sizing: border-box; margin: 0; padding: 0; }
  html, body { width: 1200px; height: 901px; overflow: hidden; background: var(--page-bg); }
  body {
    position: relative;
    font-family: "Source Sans 3", "Myriad Pro", sans-serif;
    background: radial-gradient(ellipse at 50% 40%, #0d0d0d 0%, #050505 70%, #0b0b0b 100%);
  }

  /* ---------- Top navigation ---------- */
  .feature-nav {
    position: absolute; left: 108px; top: 0; width: 957px; height: 136px;
    background: linear-gradient(180deg, var(--band-glow) 0%, var(--band-top) 45%, #080604 100%);
    box-shadow: 0 0 30px rgba(60,35,10,.35);
  }
  .nav-item {
    position: absolute; top: 0; width: 140px; margin-left: -70px;
    text-align: center;
    font-family: "Tinos", "Times New Roman", serif; font-weight: 700; font-size: 15px; line-height: 18px;
    color: var(--nav-label);
  }
  .nav-item svg { display: block; margin: 0 auto; }
  .nav-item .label { position: absolute; left: 0; right: 0; }
  .nav-item.is-active { color: var(--nav-active); }

  /* ---------- Features ---------- */
  .monitor-art {
    position: absolute; left: 108px; top: 209px; width: 390px; height: 312px;
    background: linear-gradient(135deg, var(--device-light) 0%, #262626 50%, var(--device-dark) 100%);
    border-radius: 8px;
  }
  .divider {
    position: absolute; left: 541px; top: 185px; width: 3px; height: 357px;
    background: linear-gradient(180deg, transparent, var(--divider) 30%, var(--divider) 70%, transparent);
  }
  .feature { position: absolute; width: 260px; }
  .feature h2 {
    font-family: "Tinos", "Times New Roman", serif; font-weight: 700; font-size: 20px; line-height: 22px;
    color: var(--heading-purple); letter-spacing: .2px; white-space: nowrap;
  }
  .feature p {
    margin-top: 11px; white-space: nowrap;
    font-size: 16px; line-height: 23px; color: var(--body-brown);
  }
  .feature .read-more {
    position: absolute; left: 138px; top: 128px;
    font-family: "Tinos", "Times New Roman", serif; font-size: 15px; color: var(--read-more);
    text-decoration: none; white-space: nowrap;
  }

  /* ---------- Share applications panel ---------- */
  .apps-panel {
    position: absolute; left: 108px; top: 568px; width: 957px; height: 360px;
    border-radius: 14px;
    background: linear-gradient(180deg, var(--panel-bg) 0%, #030201 65%, var(--panel-glow) 100%);
  }
  .tab {
    position: absolute; top: 586px; width: 60px; height: 330px;
    border-radius: 3px 3px 0 0;
    background: linear-gradient(180deg, var(--tab-top), var(--tab-bottom));
    display: flex; align-items: center; justify-content: center; padding-bottom: 20px;
  }
  .tab span {
    writing-mode: vertical-rl; transform: rotate(180deg);
    font-weight: 600; font-size: 23px; color: var(--tab-text); white-space: nowrap;
  }
  .apps-title {
    position: absolute; left: 293px; top: 594px;
    font-family: "Tinos", "Times New Roman", serif; font-size: 25px; font-weight: 400;
    color: var(--section-title);
  }
  .apps-copy {
    position: absolute; left: 300px; top: 647px;
    font-size: 14.5px; line-height: 23px; color: var(--light-text); white-space: nowrap;
  }
  .apps-copy p + p { margin-top: 15px; }
  .cta {
    position: absolute; left: 426px; top: 843px; width: 188px; height: 37px;
    border-radius: 3px;
    background: linear-gradient(180deg, var(--button-top), var(--button-bottom));
    font-weight: 600; font-size: 14px; color: var(--button-text);
    display: flex; align-items: center; justify-content: center; text-decoration: none;
  }
  .phone-art {
    position: absolute; left: 649px; top: 626px; width: 138px; height: 251px;
    border-radius: 22px;
    background: linear-gradient(140deg, var(--device-light) 0%, #1c1d20 50%, var(--device-dark) 100%);
  }
</style>
</head>
<body>

<nav class="feature-nav" aria-label="Features"></nav>

<a class="nav-item is-active" style="left:234px">
  <svg width="110" height="68" viewBox="0 0 110 68" aria-hidden="true">
    <circle cx="27" cy="17" r="14" fill="var(--icon-purple)"/>
    <path d="M1 67 Q1 33 27 33 Q53 33 53 67 Z" fill="var(--icon-purple)"/>
    <circle cx="82" cy="17" r="14" fill="var(--icon-purple)"/>
    <path d="M56 67 Q56 33 82 33 Q108 33 108 67 Z" fill="var(--icon-purple)"/>
  </svg>
  <span class="label" style="top:88px">Collaborate</span>
</a>

<a class="nav-item" style="left:378px">
  <svg width="80" height="68" viewBox="0 0 80 68" aria-hidden="true">
    <circle cx="30" cy="16" r="14" fill="var(--icon-dark)"/>
    <path d="M6 67 Q6 34 30 34 Q54 34 54 67 Z" fill="var(--icon-dark)"/>
    <path d="M27 36 L33 36 L35 58 L30 64 L25 58 Z" fill="#2a2a2a"/>
    <circle cx="58" cy="30" r="9" fill="none" stroke="var(--icon-dark)" stroke-width="4"/>
    <line x1="65" y1="37" x2="74" y2="46" stroke="var(--icon-dark)" stroke-width="5" stroke-linecap="round"/>
  </svg>
  <span class="label" style="top:80px">Find<br>Professionals</span>
</a>

<a class="nav-item" style="left:514px">
  <svg width="70" height="68" viewBox="0 0 70 68" aria-hidden="true">
    <ellipse cx="32" cy="10" rx="25" ry="8" fill="#1c1c1c"/>
    <path d="M7 10 L7 54 Q32 66 57 54 L57 10 Q32 20 7 10 Z" fill="var(--icon-dark)"/>
    <path d="M40 16 L40 44 Q40 50 46 50 Q52 50 52 44 L52 14 Z" fill="#1a1a1a"/>
  </svg>
  <span class="label" style="top:80px">Theme<br>Builder</span>
</a>

<a class="nav-item" style="left:655px">
  <svg width="80" height="68" viewBox="0 0 80 68" aria-hidden="true">
    <ellipse cx="40" cy="10" rx="38" ry="9" fill="var(--icon-dark)"/>
    <rect x="2" y="16" width="76" height="14" rx="7" fill="var(--icon-dark)"/>
    <rect x="2" y="34" width="76" height="14" rx="7" fill="var(--icon-dark)"/>
    <path d="M2 52 L78 52 L78 58 Q40 72 2 58 Z" fill="var(--icon-dark)"/>
  </svg>
  <span class="label" style="top:89px">Hosting</span>
</a>

<a class="nav-item" style="left:797px">
  <svg width="76" height="70" viewBox="0 0 76 70" aria-hidden="true">
    <line x1="12" y1="60" x2="58" y2="14" stroke="var(--icon-dark)" stroke-width="10" stroke-linecap="round"/>
    <circle cx="60" cy="12" r="11" fill="var(--icon-dark)"/>
    <line x1="14" y1="10" x2="62" y2="58" stroke="var(--icon-dark)" stroke-width="9" stroke-linecap="round"/>
    <rect x="4" y="2" width="18" height="12" rx="2" transform="rotate(45 13 8)" fill="var(--icon-dark)"/>
  </svg>
  <span class="label" style="top:80px">Developer<br>Tools</span>
</a>

<a class="nav-item" style="left:936px">
  <svg width="70" height="72" viewBox="0 0 70 72" aria-hidden="true">
    <g stroke="var(--icon-dark)" stroke-width="4" fill="var(--icon-dark)">
      <circle cx="35" cy="36" r="7"/>
      <line x1="35" y1="36" x2="35" y2="6"/><path d="M29 10 L35 2 L41 10 Z"/>
      <line x1="35" y1="36" x2="35" y2="66"/><path d="M29 62 L35 70 L41 62 Z"/>
      <line x1="35" y1="36" x2="5" y2="36"/><path d="M9 30 L1 36 L9 42 Z"/>
      <line x1="35" y1="36" x2="65" y2="36"/><path d="M61 30 L69 36 L61 42 Z"/>
      <line x1="35" y1="36" x2="14" y2="15"/><line x1="35" y1="36" x2="56" y2="15"/>
      <line x1="35" y1="36" x2="14" y2="57"/><line x1="35" y1="36" x2="56" y2="57"/>
    </g>
  </svg>
  <span class="label" style="top:91px">Distributions</span>
</a>

<div class="monitor-art" role="img" aria-label="Illustration area: desktop monitor on a silver stand"></div>

<div class="divider"></div>

<section class="feature" style="left:585px; top:207px">
  <h2>ASSIGN TEAM ACCESS</h2>
  <p>Dictumst purus augue, a amet,<br>lundium augue, cras, etiam<br>dipice parturient augue, tempor<br>cum pellentesque. Lectus</p>
  <a class="read-more">read more...</a>
</section>

<section class="feature" style="left:843px; top:207px">
  <h2>MANAGE PASSWORDS</h2>
  <p>Sed est sed pulvinar montes<br>arcu nec magna, turpis purus<br>ridiculus. Integer lacus egestas.</p>
  <a class="read-more">read more...</a>
</section>

<section class="feature" style="left:585px; top:383px">
  <h2>SHARE YOUR SITES</h2>
  <p>Dictumst purus augue, a amet,<br>lundium augue, cras, etiam<br>adipiscing parturient augue,<br>tempor cum pellentesque.</p>
  <a class="read-more">read more...</a>
</section>

<section class="feature" style="left:840px; top:383px">
  <h2>DISTRIBUTE WORKLOAD</h2>
  <p>Dictumst purus augue, a amet,<br>lundium augue, cras, etiam<br>adipiscing parturient augue,<br>tempor cum pellentesque.</p>
  <a class="read-more">read more...</a>
</section>

<div class="apps-panel"></div>

<div class="tab" style="left:142px"><span>Install Shared Apps</span></div>
<div class="tab" style="left:207px"><span>Share Apps</span></div>

<h2 class="apps-title">Share Aplications</h2>
<div class="apps-copy">
  <p>Montes turpis cum dignissim vel lorem tortor proin<br>mid augue. Nec eros mus adipiscing. Ac, odio<br>tincidunt augue, magnis scelerisque urna.</p>
  <p>Proin auctor integer scelerisque turpis, turpis facilisis?<br>Dolor in. In, placerat. Placerat integer pellentesque.<br>Phasellus mauris. Sed eros. Scelerisque dolor hac<br>parturient.</p>
</div>
<a class="cta">Start Now For Free!</a>

<div class="phone-art" role="img" aria-label="Illustration area: smartphone with a dark screen"></div>

<div class="tab" style="left:846px"><span>Invite Team Members</span></div>
<div class="tab" style="left:911px"><span>Per-Site Managemnt</span></div>
<div class="tab" style="left:975px"><span>Multiple Administrators</span></div>

</body>
</html>
```